High-end construction company needs a business card design

We need a modern looking business card that draws people in, is memorable and looks so good people will want to sick it on their fridges.
On the first side what is needed are:
Logo
My name - Tomasz Brelwik
Title - Managing Director
Website - www.varkelt.co.uk
Email - tomasz@varkelt.co.uk
Telephone - 020 5194 6281
Mobile - 07845139072
On the back side was is needed is a list of all the services we provide:
-Kitchen Renovations
-Bathroom Renovations
-House Renovations
-Garage Conversions
-Extensions
-Loft Conversions
-Conservatories
-Carpentry
-Tiling
-Electrical
-Plumbing & Heating
-Bricklaying
-Landscaping
-Decorating
-Plastering
We would like the colours to be the same shades as on the logo with grey or black for the words.
Target Market(s)
Anyone who needs building work done
Contact Information for Business Card
This business card is for a construction company which strives to deliver excellent service and quality.
The look and feel of the card should represent this.
Requirements
Must have
- On the first side what is needed are:
Logo
My name - Tomasz Brelwik
Title - Managing Director
Website - www.varkelt.co.uk
Email - tomasz@varkelt.co.uk
Telephone - 020 5194 6281
Mobile - 07845139072
Nice to have
- Cool looking features

```html
<!DOCTYPE html>
<html lang="en">
<head>
<meta charset="UTF-8">
<title>Varkelt Construction Ltd – Business Card</title>
<link rel="stylesheet" href="https://fonts.googleapis.com/css2?family=Montserrat:wght@400;500;700&display=swap">
<style>
  :root {
    --green-dark: #4b8c40;
    --green-light: #77bf43;
    --green-tint: #5a9a4d;
    --white: #ffffff;
    --stage: #2a2a2a;
  }
  * { box-sizing: border-box; margin: 0; padding: 0; }
  html, body { width: 1200px; height: 900px; overflow: hidden; }
  body {
    background: var(--stage);
    font-family: "Montserrat", sans-serif;
    display: flex; flex-direction: column; align-items: center; justify-content: center;
    gap: 48px;
  }
  .card {
    position: relative;
    width: 660px; height: 377px;
    border-radius: 22px;
    overflow: hidden;
  }
  /* back side */
  .card--services { background: var(--green-dark); color: var(--white); }
  .skyline {
    position: absolute; left: 0; right: 0; bottom: 0; height: 190px;
    background: linear-gradient(to top, rgba(255,255,255,0.08), rgba(255,255,255,0.02));
  }
  .services-inner {
    position: relative; height: 100%;
    display: flex; flex-direction: column; align-items: center;
    padding-top: 62px;
  }
  .brand {
    display: flex; align-items: center; gap: 10px;
    font-weight: 700; font-size: 30px; letter-spacing: 1px; text-transform: uppercase;
  }
  .brand__mark { width: 18px; height: 18px; background: currentColor; }
  .brand__sub { font-size: 11px; letter-spacing: 2px; }
  .services-title {
    margin-top: 30px; font-size: 19px; font-weight: 500;
    padding-bottom: 6px; border-bottom: 2px solid var(--white);
  }
  .services-list { margin-top: 24px; display: flex; flex-direction: column; gap: 12px; align-items: center; }
  .services-row { display: flex; gap: 14px; list-style: none; font-size: 12.5px; }
  .services-row li::before { content: "\2022"; margin-right: 6px; }

  /* front side */
  .card--contact { background: var(--white); }
  .card-shapes { position: absolute; inset: 0; }
  .front-brand {
    position: absolute; right: 40px; top: 50px;
    color: var(--green-light); text-align: right;
  }
  .front-brand .brand { font-size: 32px; justify-content: flex-end; }
  .person {
    position: absolute; right: 40px; top: 175px; text-align: right; color: var(--white);
  }
  .person__name { font-size: 28px; font-weight: 700; }
  .person__title { font-size: 13px; margin-top: 2px; }
  .contact-list {
    position: absolute; left: 150px; bottom: 36px;
    list-style: none; color: var(--white); font-size: 15px;
    display: flex; flex-direction: column; gap: 5px;
  }
  .contact-list li { display: flex; align-items: center; gap: 12px; }
  .contact-list svg { width: 14px; height: 14px; fill: var(--white); flex: none; }
</style>
</head>
<body>

<section class="card card--services">
  <div class="skyline" role="img" aria-label="Faint city skyline silhouette"></div>
  <div class="services-inner">
    <div class="brand"><span class="brand__mark"></span>Varkelt Construction Ltd</div>
    <h2 class="services-title">Our Services</h2>
    <div class="services-list">
      <ul class="services-row">
        <li>Kitchen Renovations</li><li>Bathroom Renovations</li><li>House Renovations</li><li>Plastering</li>
      </ul>
      <ul class="services-row">
        <li>Garage Conversions</li><li>Plumbing &amp; Heating</li><li>Carpentry</li><li>Landscaping</li><li>Tiling</li>
      </ul>
      <ul class="services-row">
        <li>Conservatories</li><li>Electrical</li><li>Extensions</li><li>Bricklaying</li><li>Decorating</li><li>Loft Conversions</li>
      </ul>
    </div>
  </div>
</section>

<section class="card card--contact">
  <svg class="card-shapes" viewBox="0 0 660 377" preserveAspectRatio="none">
    <polygon points="0,236 190,142 660,98 660,112 210,162 110,222 0,251" fill="var(--green-light)"/>
    <polygon points="0,263 660,120 660,377 0,377" fill="var(--green-dark)"/>
    <polyline points="150,222 210,170 420,162 150,222" fill="none" stroke="var(--white)" stroke-width="5"/>
  </svg>

  <div class="front-brand">
    <div class="brand"><span class="brand__mark"></span>Varkelt</div>
    <div class="brand__sub">Construction Ltd</div>
  </div>

  <div class="person">
    <div class="person__name">Tomasz Brelwik</div>
    <div class="person__title">Managing Director</div>
  </div>

  <ul class="contact-list">
    <li><svg viewBox="0 0 24 24"><path d="M3 8c3-4 15-4 18 0l-3 3-3-2V7H9v2l-3 2zM6 12h12l2 8H4z"/></svg>020 5194 6281</li>
    <li><svg viewBox="0 0 24 24"><path d="M7 2h10v20H7zM9 4v14h6V4z"/></svg>07845139072</li>
    <li><svg viewBox="0 0 24 24"><path d="M2 5h20v14H2zM4 7l8 6 8-6v-0H4z"/></svg>tomasz@varkelt.co.uk</li>
    <li><svg viewBox="0 0 24 24"><circle cx="12" cy="12" r="10"/><path d="M2 12h20M12 2c4 4 4 16 0 20M12 2c-4 4-4 16 0 20" stroke="var(--green-dark)" stroke-width="1.5" fill="none"/></svg>www.varkelt.co.uk</li>
  </ul>
</section>

</body>
</html>
```